BRAVO Estate Attendant

We require a website built for this company. Logo is also on the attached document. Some info on the company:<br/>To create a work class experience for our clients for property maintenance. A personalised service that deliver’s what landlords need...Quality work, on time and managed from start to finish.<br/>We do things different, our clients deal with one contact, a client manager who manages your maintenance task from start to finish. Our service allows our expert trades people to do what they do best and leave the management/organising to us!<br/>I have drafted up the layout of the web ... very brief at this stage however once we have more info we will add links and can collate more information and provide. <br/>We just want to get a layout of what you think the web should look like and can go from there.

```html
<!DOCTYPE html>
<html lang="en">
<head>
<meta charset="utf-8">
<title>BRAVO Estate Attendant</title>
<link href="https://fonts.googleapis.com/css2?family=Poppins:wght@400;500;600;700&display=swap" rel="stylesheet">
<style>
:root{
  --yellow:#fdbf0f;
  --orange:#f4a40b;
  --dark:#333333;
  --ink:#222222;
  --body:#555555;
  --muted:#888888;
  --line:#e6e6e6;
  --soft:#f6f6f6;
  --mist:#f0f2f4;
  --footer:#454545;
  --topbar:#3b3b3b;
  --navy:#1e3d7a;
}
*{box-sizing:border-box;margin:0;padding:0}
html,body{width:1200px;height:2625px;overflow:hidden}
body{font-family:"Poppins",sans-serif;color:var(--body);background:#fff;position:relative}
.wrap{position:absolute;left:234px;width:732px}

/* top bar */
.topbar{position:absolute;top:0;left:0;width:1200px;height:32px;background:var(--topbar);font-size:9px;color:#fff}
.topbar .client{position:absolute;left:0;top:0;width:397px;height:32px;background:var(--yellow);padding-left:236px;line-height:32px;font-weight:600}
.topbar .mail{position:absolute;left:676px;top:0;line-height:32px}
.topbar .mail b{font-weight:600}
.social{position:absolute;top:12px;left:894px;display:flex;gap:8px}
.social span{width:8px;height:8px;background:#fff;border-radius:50%}

/* header */
.header{position:absolute;top:32px;left:0;width:1200px;height:72px;border-bottom:1px solid var(--line)}
.brand{position:absolute;left:234px;top:18px;font-size:22px;font-weight:700;color:var(--ink);line-height:1.1;letter-spacing:.5px}
.nav{position:absolute;left:546px;top:0;height:72px;display:flex;align-items:center;gap:27px;font-size:10px;font-weight:600;color:var(--ink)}
.nav .active{color:var(--yellow)}
.nav .sep{width:1px;height:20px;background:var(--line);margin-left:-6px}
.search{width:18px;height:18px;border-radius:50%;background:#eee;margin-left:-12px;display:flex;align-items:center;justify-content:center}

/* hero */
.hero{position:absolute;top:104px;left:0;width:1200px;height:450px;background:linear-gradient(120deg,#6a5a45 0%,#3f3a35 45%,#2c2a28 70%,#5a4a34 100%)}
.hero-title{position:absolute;left:0;width:1200px;top:150px;text-align:center;color:#fff;font-size:54px;font-weight:600;letter-spacing:-1px}
.hero-sub{position:absolute;left:0;width:1200px;top:268px;text-align:center;color:#fff;font-size:16px;line-height:23px}
.arrow{position:absolute;top:206px;width:34px;height:34px;background:#fff;display:flex;align-items:center;justify-content:center}
.dots{position:absolute;display:flex;gap:4px}
.dots span{width:22px;height:2px;background:rgba(255,255,255,.5)}
.dots span.on{background:#fff}

/* welcome */
.welcome{position:absolute;top:554px;left:0;width:1200px;height:396px;background:#fff}
.kicker{font-size:11px;font-weight:600;color:var(--muted);margin-left:27px}
.kicker-dots{position:absolute;left:0;top:4px;width:12px;height:4px;border-top:2px dotted var(--yellow)}
.welcome h2{font-size:14px;font-weight:600;color:var(--ink);margin:6px 0 0 27px}
.lead{font-size:10px;font-weight:600;color:var(--ink);line-height:17.5px;margin-top:18px}
.copy{font-size:10px;line-height:17.5px;margin-top:18px;color:var(--body)}
.frame{position:absolute;left:840px;top:58px;width:132px;height:98px;border-top:6px solid var(--dark);border-right:6px solid var(--dark)}
.video{position:absolute;left:609px;top:64px;width:357px;height:266px;background:linear-gradient(135deg,#c9ccd0,#e7e6df 55%,#b58a5a)}
.play{position:absolute;left:156px;top:110px;width:46px;height:46px;border-radius:50%;background:var(--yellow);display:flex;align-items:center;justify-content:center}

/* sections common */
.sec-title{position:absolute;left:0;width:1200px;text-align:center;font-size:18px;font-weight:700;color:var(--dark)}
.sec-title em{font-style:normal;color:var(--yellow)}
.sec-dots{position:absolute;left:594px;width:12px;height:4px;border-top:2px dotted var(--yellow)}

/* services */
.services{position:absolute;top:950px;left:0;width:1200px;height:535px;background:linear-gradient(90deg,#eeeeee,#f8f8f8 30%,#f8f8f8 70%,#eeeeee)}
.svc{position:absolute;width:232px;height:173px;background:#fff;padding:18px 21px;border:1px solid #f0f0f0}
.svc-head{display:flex;align-items:center;gap:13px;height:40px}
.svc-icon{width:40px;height:38px;background:#e4e4e4;border-radius:4px;flex:none}
.svc h3{font-size:11px;font-weight:600;color:var(--ink);line-height:14px}
.svc p{font-size:8.6px;line-height:16.3px;margin-top:9px}

/* team */
.team{position:absolute;top:1485px;left:0;width:1200px;height:447px;background:#fff}
.member{position:absolute;top:122px;width:232px;height:263px}
.photo{height:209px}
.name{height:54px;background:var(--yellow);color:#fff;font-size:12px;font-weight:600;text-align:center;line-height:54px}
.member-social{position:absolute;left:0;top:155px;width:232px;height:54px;background:rgba(240,240,240,.85);display:flex;justify-content:center;align-items:center;gap:14px}
.member-social span{width:14px;height:14px;border-radius:50%;background:var(--dark)}

/* testimonials */
.clients{position:absolute;top:1932px;left:0;width:1200px;height:403px;background:var(--mist)}
.quote{position:absolute;top:120px;width:232px;height:183px;background:#fff;border:1px solid #e3e3e3;padding:16px 21px}
.q-top{display:flex;justify-content:space-between;align-items:center}
.q-mark{font-size:22px;font-weight:700;color:var(--dark);line-height:16px}
.stars{display:flex;gap:6px}
.stars svg{width:11px;height:11px}
.quote p{font-size:8.6px;line-height:15px;margin-top:12px}
.who{display:flex;align-items:center;gap:12px;margin-top:16px}
.avatar{width:48px;height:48px;border-radius:50%;background:linear-gradient(135deg,#c9b9a4,#6d6259)}
.who b{display:block;font-size:11px;font-weight:600;color:var(--ink)}
.who span{font-size:10px;color:var(--navy)}

/* footer */
.footer{position:absolute;top:2335px;left:0;width:1200px;height:290px;background:var(--footer);color:#ddd;font-size:9px}
.f-brand{position:absolute;left:234px;top:52px;font-size:22px;font-weight:700;color:#fff;line-height:1.1}
.f-about{position:absolute;left:234px;top:113px;width:166px;line-height:15.7px;color:#ddd}
.f-col{position:absolute;top:50px}
.f-col h4{font-size:9.5px;font-weight:600;color:#fff;margin-bottom:12px}
.f-col li{list-style:none;line-height:18.7px}
.f-info li{display:flex;gap:10px;align-items:flex-start;margin-bottom:5px}
.f-info svg{width:10px;height:10px;flex:none;margin-top:4px}
.f-rule{position:absolute;left:234px;top:230px;width:732px;height:1px;background:#5a5a5a}
.f-copy{position:absolute;left:234px;top:252px;color:#aaa}
.f-legal{position:absolute;left:810px;top:252px;color:#aaa}
.mailbtn{position:absolute;left:1100px;top:2521px;width:41px;height:41px;border-radius:50%;background:var(--yellow);display:flex;align-items:center;justify-content:center}
</style>
</head>
<body>

<div class="topbar">
  <div class="client">Client Services: 02 7100 4821</div>
  <div class="mail"><b>Email:</b> hello@bravoattendant.example</div>
  <div class="social"><span></span><span></span><span></span><span></span></div>
</div>

<header class="header">
  <div class="brand">BRAVO<br><span style="font-size:9px">ESTATE ATTENDANT</span></div>
  <nav class="nav">
    <span class="active">HOME</span>
    <span>ABOUT US</span>
    <span>SERVICES ⌄</span>
    <span>BENEFIT ⌄</span>
    <span>CONTACT US</span>
    <span class="sep"></span>
    <span class="search"><svg width="8" height="8" viewBox="0 0 10 10"><circle cx="4" cy="4" r="3" fill="none" stroke="#555" stroke-width="1.3"/><line x1="6.3" y1="6.3" x2="9" y2="9" stroke="#555" stroke-width="1.3"/></svg></span>
  </nav>
</header>

<section class="hero" role="img" aria-label="Desk with building plans, tape measure, hammer and hard hat">
  <div class="hero-title">BRAVO<div style="font-size:20px;font-weight:600;letter-spacing:0;margin-top:-6px">ESTATE ATTENDANT</div></div>
  <p class="hero-sub">Wealth management and financial advisory company with a<br>strong commitment to the local community</p>
  <div class="arrow" style="left:93px"><svg width="10" height="10" viewBox="0 0 10 10"><path d="M6.5 1.5 3 5l3.5 3.5" fill="none" stroke="#333" stroke-width="1.3"/></svg></div>
  <div class="arrow" style="left:1074px"><svg width="10" height="10" viewBox="0 0 10 10"><path d="M3.5 1.5 7 5 3.5 8.5" fill="none" stroke="#333" stroke-width="1.3"/></svg></div>
  <div class="dots" style="left:564px;top:406px"><span class="on"></span><span></span><span></span></div>
</section>

<section class="welcome">
  <div class="wrap" style="top:80px;width:335px">
    <div class="kicker-dots"></div>
    <div class="kicker">WELCOME TO</div>
    <h2>BRAVO ESTATE ATTENDANT</h2>
    <p class="lead">Lorem ipsum dolor sit amet, consectetur adipiscing elit. Cras vitae orci lacinia dolor porta elementum vitae non nisl. Duis porttitor rutrum rhoncus.</p>
    <p class="copy">Cras neque tellus, hendrerit nec tristique ut, dictum ac massa. Vivamus semper leo vel pellentesque suscipit. Mauris eget purus ligula. Sed nisl risus, mattis id risus tempus, sagittis tempor eros. In hac habitasse platea dictumst. Curabitur ac risus non ante fringilla tincidunt sit amet vitae ligula. Donec lacus tellus, gravida eu augue a, sollicitudin scelerisque turpis. Quisque at leo non metus posuere ultrices id non sem.</p>
  </div>
  <div class="frame"></div>
  <div class="video" role="img" aria-label="Team reviewing floor plans on a desk">
    <div class="play"><svg width="16" height="16" viewBox="0 0 16 16"><path d="M4 2.5v11L13 8z" fill="none" stroke="#fff" stroke-width="1.6"/></svg></div>
  </div>
</section>

<section class="services">
  <div class="sec-dots" style="top:49px"></div>
  <h2 class="sec-title" style="top:60px">OUR <em>SERVICES</em></h2>

  <div class="svc" style="left:234px;top:119px"><div class="svc-head"><div class="svc-icon" role="img" aria-label="Trade people icon"></div><h3>Trade People</h3></div><p>Lorem ipsum dolor sit amet, consectetur adipiscing elit. Cras vitae orci lacinia dolor porta elementum vitae non nisl. Duis porttitor rutrum rhoncus. Orci varius natoque penatibus et magnis dis parturient montes</p></div>
  <div class="svc" style="left:484px;top:119px"><div class="svc-head"><div class="svc-icon" role="img" aria-label="Removal truck icon"></div><h3>Removalist Van and Trailers</h3></div><p>Lorem ipsum dolor sit amet, consectetur adipiscing elit. Cras vitae orci lacinia dolor porta elementum vitae non nisl. Duis porttitor rutrum rhoncus. Orci varius natoque penatibus et magnis dis parturient montes</p></div>
  <div class="svc" style="left:734px;top:119px"><div class="svc-head"><div class="svc-icon" role="img" aria-label="Network connections icon"></div><h3>Connections</h3></div><p>Lorem ipsum dolor sit amet, consectetur adipiscing elit. Cras vitae orci lacinia dolor porta elementum vitae non nisl. Duis porttitor rutrum rhoncus. Orci varius natoque penatibus et magnis dis parturient montes</p></div>
  <div class="svc" style="left:234px;top:309px"><div class="svc-head"><div class="svc-icon" role="img" aria-label="Smoke alarm icon"></div><h3>Smoke Alarms</h3></div><p>Lorem ipsum dolor sit amet, consectetur adipiscing elit. Cras vitae orci lacinia dolor porta elementum vitae non nisl. Duis porttitor rutrum rhoncus. Orci varius natoque penatibus et magnis dis parturient montes</p></div>
  <div class="svc" style="left:484px;top:309px"><div class="svc-head"><div class="svc-icon" role="img" aria-label="Briefcase icon"></div><h3>Finance</h3></div><p>Lorem ipsum dolor sit amet, consectetur adipiscing elit. Cras vitae orci lacinia dolor porta elementum vitae non nisl. Duis porttitor rutrum rhoncus. Orci varius natoque penatibus et magnis dis parturient montes</p></div>
  <div class="svc" style="left:734px;top:309px"><div class="svc-head"><div class="svc-icon" role="img" aria-label="Diamond icon"></div><h3>Wealth Creation</h3></div><p>Lorem ipsum dolor sit amet, consectetur adipiscing elit. Cras vitae orci lacinia dolor porta elementum vitae non nisl. Duis porttitor rutrum rhoncus. Orci varius natoque penatibus et magnis dis parturient montes</p></div>
</section>

<section class="team">
  <div class="sec-dots" style="top:53px"></div>
  <h2 class="sec-title" style="top:64px">OUR <em>TEAM</em></h2>
  <div class="member" style="left:234px">
    <div class="photo" role="img" aria-label="Portrait of a worker in a yellow hard hat" style="background:linear-gradient(180deg,#6e6e6e,#a9a9a9)"></div>
    <div class="member-social"><span></span><span></span><span></span><span></span></div>
    <div class="name">OWEN MARSH</div>
  </div>
  <div class="member" style="left:484px">
    <div class="photo" role="img" aria-label="Portrait of a worker in a blue hard hat" style="background:linear-gradient(180deg,#b89a74,#2c3340)"></div>
    <div class="name">TARA WILDE</div>
  </div>
  <div class="member" style="left:734px">
    <div class="photo" role="img" aria-label="Portrait of a worker in a white hard hat" style="background:linear-gradient(180deg,#eeeeee,#3d7fc4)"></div>
    <div class="name">LUKE FENTON</div>
  </div>
</section>

<section class="clients">
  <div class="sec-dots" style="top:50px"></div>
  <h2 class="sec-title" style="top:61px">OUR <em>CLIENTS SAY</em></h2>

  <div class="quote" style="left:233px">
    <div class="q-top"><span class="q-mark">”</span><div class="stars"><svg viewBox="0 0 10 10"><path d="M5 .5l1.3 3 3.2.3-2.4 2.1.7 3.1L5 7.4 2.2 9l.7-3.1L.5 3.8l3.2-.3z" fill="#f4a40b"/></svg><svg viewBox="0 0 10 10"><path d="M5 .5l1.3 3 3.2.3-2.4 2.1.7 3.1L5 7.4 2.2 9l.7-3.1L.5 3.8l3.2-.3z" fill="#f4a40b"/></svg><svg viewBox="0 0 10 10"><path d="M5 .5l1.3 3 3.2.3-2.4 2.1.7 3.1L5 7.4 2.2 9l.7-3.1L.5 3.8l3.2-.3z" fill="#f4a40b"/></svg><svg viewBox="0 0 10 10"><path d="M5 .5l1.3 3 3.2.3-2.4 2.1.7 3.1L5 7.4 2.2 9l.7-3.1L.5 3.8l3.2-.3z" fill="#f4a40b"/></svg><svg viewBox="0 0 10 10"><path d="M5 .5l1.3 3 3.2.3-2.4 2.1.7 3.1L5 7.4 2.2 9l.7-3.1L.5 3.8l3.2-.3z" fill="#f4a40b"/></svg></div></div>
    <p>Lorem ipsum dolor sit amet, consectetur adipiscing elit. Quisque iaculis elementum eleifend. Cras malesuada vitae enim id imperdiet. Vestibulum vestibulum egestas.</p>
    <div class="who"><div class="avatar" role="img" aria-label="Client photo"></div><div><b>SIMON HALE</b><span>Client</span></div></div>
  </div>
  <div class="quote" style="left:483px">
    <div class="q-top"><span class="q-mark">”</span><div class="stars"><svg viewBox="0 0 10 10"><path d="M5 .5l1.3 3 3.2.3-2.4 2.1.7 3.1L5 7.4 2.2 9l.7-3.1L.5 3.8l3.2-.3z" fill="#f4a40b"/></svg><svg viewBox="0 0 10 10"><path d="M5 .5l1.3 3 3.2.3-2.4 2.1.7 3.1L5 7.4 2.2 9l.7-3.1L.5 3.8l3.2-.3z" fill="#f4a40b"/></svg><svg viewBox="0 0 10 10"><path d="M5 .5l1.3 3 3.2.3-2.4 2.1.7 3.1L5 7.4 2.2 9l.7-3.1L.5 3.8l3.2-.3z" fill="#f4a40b"/></svg><svg viewBox="0 0 10 10"><path d="M5 .5l1.3 3 3.2.3-2.4 2.1.7 3.1L5 7.4 2.2 9l.7-3.1L.5 3.8l3.2-.3z" fill="#f4a40b"/></svg><svg viewBox="0 0 10 10"><path d="M5 .5l1.3 3 3.2.3-2.4 2.1.7 3.1L5 7.4 2.2 9l.7-3.1L.5 3.8l3.2-.3z" fill="#f4a40b"/></svg></div></div>
    <p>Lorem ipsum dolor sit amet, consectetur adipiscing elit. Quisque iaculis elementum eleifend. Cras malesuada vitae enim id imperdiet. Vestibulum vestibulum egestas.</p>
    <div class="who"><div class="avatar" role="img" aria-label="Client photo" style="background:linear-gradient(135deg,#d8d8d8,#7a7a7a)"></div><div><b>SIMON HALE</b><span>Client</span></div></div>
  </div>
  <div class="quote" style="left:733px">
    <div class="q-top"><span class="q-mark">”</span><div class="stars"><svg viewBox="0 0 10 10"><path d="M5 .5l1.3 3 3.2.3-2.4 2.1.7 3.1L5 7.4 2.2 9l.7-3.1L.5 3.8l3.2-.3z" fill="#f4a40b"/></svg><svg viewBox="0 0 10 10"><path d="M5 .5l1.3 3 3.2.3-2.4 2.1.7 3.1L5 7.4 2.2 9l.7-3.1L.5 3.8l3.2-.3z" fill="#f4a40b"/></svg><svg viewBox="0 0 10 10"><path d="M5 .5l1.3 3 3.2.3-2.4 2.1.7 3.1L5 7.4 2.2 9l.7-3.1L.5 3.8l3.2-.3z" fill="#f4a40b"/></svg><svg viewBox="0 0 10 10"><path d="M5 .5l1.3 3 3.2.3-2.4 2.1.7 3.1L5 7.4 2.2 9l.7-3.1L.5 3.8l3.2-.3z" fill="#f4a40b"/></svg><svg viewBox="0 0 10 10"><path d="M5 .5l1.3 3 3.2.3-2.4 2.1.7 3.1L5 7.4 2.2 9l.7-3.1L.5 3.8l3.2-.3z" fill="#f4a40b"/></svg></div></div>
    <p>Lorem ipsum dolor sit amet, consectetur adipiscing elit. Quisque iaculis elementum eleifend. Cras malesuada vitae enim id imperdiet. Vestibulum vestibulum egestas.</p>
    <div class="who"><div class="avatar" role="img" aria-label="Client photo" style="background:linear-gradient(135deg,#8a6a4a,#3a2e28)"></div><div><b>SIMON HALE</b><span>Client</span></div></div>
  </div>

  <div class="dots" style="left:564px;top:349px"><span style="background:var(--yellow)"></span><span style="background:#333"></span><span style="background:#333"></span></div>
</section>

<footer class="footer">
  <div class="f-brand">BRAVO<br><span style="font-size:9px">ESTATE ATTENDANT</span></div>
  <p class="f-about">Lorem ipsum dolor sit amet, consectetur adipiscing elit. Cras vitae orci lacinia dolor porta elementum vitae non nisl. Duis porttitor rutrum rhoncus.</p>

  <div class="f-col" style="left:430px"><h4>QUICK LINKS</h4><ul><li>Home</li><li>About Us</li><li>Services</li><li>Benefit</li><li>Contact Us</li></ul></div>
  <div class="f-col" style="left:534px"><h4>SERVICES</h4><ul><li>Trade People</li><li>Removalist Van and Trailers</li><li>Connections</li><li>Smoke Alarms</li><li>Finance</li><li>Wealth Creation</li></ul></div>
  <div class="f-col" style="left:688px"><h4>BENEFIT</h4><ul><li>Customer Service</li><li>Call Centre</li><li>Values</li><li>Pricing</li><li>Level of Expertise</li></ul></div>
  <div class="f-col f-info" style="left:797px;top:47px"><h4>CONTACT INFO</h4><ul>
    <li><svg viewBox="0 0 10 10"><path d="M2 1h2l1 2.5-1.2 1a5 5 0 0 0 2.2 2.2L7 5.5 9.5 6.5v2A1 1 0 0 1 8.5 9.5 8 8 0 0 1 .5 1.5 1 1 0 0 1 2 1z" fill="#fff"/></svg>02 7100 4821</li>
    <li><svg viewBox="0 0 10 10"><rect x=".5" y="2" width="9" height="6.5" fill="#fff"/><path d="M.8 2.3 5 5.5l4.2-3.2" fill="none" stroke="#454545" stroke-width=".9"/></svg>hello@bravoattendant.example</li>
    <li><svg viewBox="0 0 10 10"><path d="M5 .5a3.3 3.3 0 0 0-3.3 3.3C1.7 6.3 5 9.5 5 9.5s3.3-3.2 3.3-5.7A3.3 3.3 0 0 0 5 .5z" fill="#fff"/><circle cx="5" cy="3.8" r="1.2" fill="#454545"/></svg>8/14 Harbour Lane,<br>Seaview NSW</li>
  </ul></div>

  <div class="f-rule"></div>
  <div class="f-copy">Copyright © 2019 BRAVO Estate Attendant All rights reserved.</div>
  <div class="f-legal">Terms &amp; Conditions &nbsp;|&nbsp; Privacy Policy</div>
</footer>

<div class="mailbtn"><svg width="18" height="14" viewBox="0 0 18 14"><rect x="1" y="1" width="16" height="12" rx="1" fill="none" stroke="#fff" stroke-width="1.6"/><path d="M1.5 1.8 9 7.5l7.5-5.7" fill="none" stroke="#fff" stroke-width="1.6"/></svg></div>

</body>
</html>
```